Schlichtes Design für Malerbetrieb
Zielgruppe
Wir sind ein mittelgroßer Malerbetrieb in München mit umfangreichem Leistungsspektrum.
Unsere Hauptleistungen sind: Fassadenrenovierung, Altbausanierung, Betoninstandsetzung, Balkonabdichtung (kein Neubau!).
Unsere Zielgruppen sind: Hausverwaltungen, Firmen und Privatpersonen.
Unsere Kunden schätzen: Konstruktive Organisation und Planung im Vorfeld, Zuverlässigkeit, saubere Arbeitsweise, dauerhafte Balkonabdichtungen.
Aufgabenstellung
Wir möchten eine langlebige, stilvolle, minimalistische Homepage.
Wir möchten von der bestehenden Homepage nur die Schriftart für unseren Firmennamen (Century Gothic) und wenn möglich (nicht zwingend), irgendwo das florale Muster einbauen. Corporate-Design haben wir nicht.
Farbtöne: Firmennamen Orange (hellorange bis erdiges Orange möglich, da sind wir nicht fixiert) , einen dunklen Hintergrundfarbton (Petrol-Blaugrau ?) mit gelbem (neon bis senfgelb) Akzent (Linien), Blumenmuster weiß, grau.
Dies sind nur unsere Ideen. Wir sind aber auch absolut offen für eure Profi-Ideen.
Wir möchten uns von den unzähligen langweiligen 'Pinselseiten mit veralteten Bilder' unserer Kollegen interessant und mit Stil abheben.
Eher nach dem Motto 'weniger ist mehr'.
Einen positiven, sympathischen Eindruck geben und unsere Leistungen in den Vordergrund bringen.
Da wir viele Stammkunden haben, betreiben wir kein Social-Media und möchten dies vorerst auch nicht tun.
Die Seite wird in den nächsten Jahren nicht verändert, höchstens die Bilder aktualisiert.
Die Texte haben wir alle selbst entworfen und möchten wir so übernehmen.
Die Galerien sollen unkompliziert anzuschauen sein.
Uns gefällt die Struktur und Schlichtheit von https://vaartmolen.nl/ oder Timbra.de gut und wir mögen Vintage-Grafiken gerne.
Einerseits darf die Seite geradlinig, andererseits aber auch rund und floral wirken.

```html
<!DOCTYPE html>
<html lang="de">
<head>
<meta charset="utf-8">
<title>Kolbrit Malerarbeiten</title>
<link rel="stylesheet" href="https://fonts.googleapis.com/css2?family=Encode+Sans+Condensed:wght@400;500&display=swap">
<style>
  :root {
    --bar: #59585a;
    --pattern: #6c6b6e;
    --teal: #007a96;
    --mustard: #d9c95a;
    --stone: #8a8a8c;
    --white: #ffffff;
  }
  html, body { margin: 0; padding: 0; overflow: hidden; }
  body { width: 1200px; height: 900px; position: relative; background: var(--bar); }
  .page { position: relative; width: 1200px; height: 900px; overflow: hidden; }

  .site-header {
    position: absolute; top: 0; left: 0; width: 1200px; height: 125px;
    background: var(--bar);
  }
  .header-brand {
    position: absolute; right: 52px; top: 20px; margin: 0;
    font-family: "Encode Sans Condensed", sans-serif;
    font-size: 44px; font-weight: 500; color: var(--mustard); line-height: 1;
  }
  .main-nav {
    position: absolute; left: 48px; right: 52px; top: 92px;
    display: flex; justify-content: space-between;
    font-family: "Encode Sans Condensed", sans-serif;
    font-size: 22px; font-weight: 500; color: var(--white); line-height: 1;
  }
  .main-nav a { color: inherit; text-decoration: none; }

  .hero { position: absolute; top: 125px; left: 0; width: 1200px; height: 715px; }
  .hero-shapes { position: absolute; inset: 0; width: 1200px; height: 715px; }

  .hero-brand { position: absolute; left: 114px; top: 222px; }
  .hero-name {
    margin: 0; font-family: "Encode Sans Condensed", sans-serif;
    font-size: 100px; font-weight: 500; color: var(--mustard); line-height: 1;
  }
  .hero-trade {
    margin: 14px 0 0 4px; font-family: "Encode Sans Condensed", sans-serif;
    font-size: 26px; font-weight: 500; color: var(--white); line-height: 1;
  }

  .site-footer {
    position: absolute; bottom: 0; left: 0; width: 1200px; height: 60px;
    background: var(--bar);
  }
  .footer-nav {
    position: absolute; right: 22px; top: 18px; display: flex; gap: 24px;
    font-family: "Encode Sans Condensed", sans-serif;
    font-size: 23px; font-weight: 500; color: var(--white); line-height: 1;
  }
  .footer-nav a { color: inherit; text-decoration: none; }
</style>
</head>
<body>
<div class="page">
  <header class="site-header">
    <p class="header-brand">Kolbrit</p>
    <nav class="main-nav">
      <a href="#">malerarbeiten</a>
      <a href="#">betoninstandsetzung</a>
      <a href="#">balkonabdichtung</a>
      <a href="#">farbgestaltung</a>
      <a href="#">wärmedämmung</a>
      <a href="#">ausbildung</a>
      <a href="#">portrait</a>
    </nav>
  </header>

  <section class="hero">
    <svg class="hero-shapes" viewBox="0 107 1024 610" preserveAspectRatio="none" xmlns="http://www.w3.org/2000/svg">
      <rect x="0" y="107" width="1024" height="610" fill="var(--pattern)" role="img" aria-label="Florales Damast-Muster in Grautönen"/>
      <polygon points="0,107 215,107 725,355 272,580 0,448" fill="var(--teal)"/>
      <polygon points="0,448 550,717 0,717" fill="var(--stone)"/>
      <polygon points="1024,213 1024,712 510,463" fill="var(--mustard)"/>
    </svg>
    <div class="hero-brand">
      <h1 class="hero-name">Kolbrit</h1>
      <p class="hero-trade">Malerarbeiten</p>
    </div>
  </section>

  <footer class="site-footer">
    <nav class="footer-nav">
      <a href="#">Kontakt</a>
      <a href="#">Impressum</a>
      <a href="#">Datenschutz</a>
    </nav>
  </footer>
</div>
</body>
</html>
```